Flyer for handout on the street to attract people

Create two different leaflets for handing out to recruit volunteers to participate in a program of biological specimen donation. The leaflet should be catchy, have some graphics, and have enough info that people will want to sign up by going to the website for more information.

Leave room on each leaflet for some English and Chinese. The example of Leaflet #1 will need approximately the same space in order to have the Chinese translation.

The example of Leaflet #2 already has a Chinese translation which can be incorporated.

The size should be half of A4 page. If it is a whole A4 page it may also be considered.

Leaflet #1 Text:

RECRUITING HEALTHY VOLUNTEERS (and get PAID)!

The Orient Floracell Reserve is recruiting healthy individuals in Hong Kong to participate in a scientific research project to study bacteria in healthy guts. They will pay you $200 HKD per day to participate in the study. If you qualify, you can earn up to $4800 a month!

Incidences of digestive and colon diseases are increasing rapidly in Hong Kong, and part of the key to solving this problem is understanding gut bacteria. There are up to 100 trillion bacteria and microbes in every human gut, including yours. Scientists have recently uncovered that these bacteria are key human digestion and immune systems. However, when your gut bacteria are imbalanced, it can cause all kinds of problems such as indigestion, IBS, ulcerative colitis, or clostridium difficile infection.

Every year, more than 500,000 people are infected by a toxic bacteria called clostridium difficile, which causes severe stomach pain, and sometimes even death. YOUR GUT BACTERIA COULD BE KEY TO HELPING THESE SICK PATIENTS.

CRITERIA FOR PARTICIPATING: If you are a healthy adult between 18-50 years old; no digestive problems and no recent medications, then the Orient VitaVault needs your participation! They will pay you $200 HKD per day to participate in the study. If you qualify, you can earn up to $4800 a month! To learn more information, go to http://www.orientvitavault.example or send a whatsapp to 7342 9086

Leaflet #2 Text:

Get paid to give your poopoo!

Literally.

Asia’s first commercial stool bank is recruiting donors. Get paid up to $4,800 HKD per month for your poop donations at our convenient Central Hong Kong lab.

Answer the questionnaire to see if you qualify at www.orientvitavault.example or call 7342 9086 for more information.

你好屎!

我地就係想要你D好屎。

全亞洲第一間商業糞便銀行正招募捐贈者。請即前往我們位於中環的糞便銀行成為捐贈者,每月最多可賺取6,000港元的酬勞。

想知道自己是否適合捐贈?馬上點擊 www.orientvitavault.example/donate 回答問題或撥打0000-0000查詢詳情。

Target Market(s)

Young professionals, middle-class

Industry/Entity Type

Medical

Font styles to use
Serif
Sans Serif
Decorative

Requirements
Must have
• The text. Two leaflet examples. Some graphics.
Nice to have
• Catchy design. Something people will see while walking past and go ahead and take it from someone handing out flyers.
Should not have
• Only text. Should be colorful and have graphics. (Can download or shutterstock photos.)

```html
<!DOCTYPE html>
<html lang="en">
<head>
<meta charset="utf-8">
<title>Orient Floracell Reserve – Volunteer Leaflets</title>
<link href="https://fonts.googleapis.com/css2?family=Oswald:wght@400;500&family=Open+Sans:ital,wght@0,400;0,600;1,400&family=Noto+Sans+TC:wght@400&display=swap" rel="stylesheet">
<style>
  :root{
    --pink:#e0479b;
    --blue:#2f4b8f;
    --purple:#6b4b9e;
    --ink:#222;
    --muted:#444;
    --mist:#eceef1;
    --photo-a:#cfd8e3;
    --photo-b:#eef1f5;
  }
  *{margin:0;padding:0;box-sizing:border-box}
  html,body{width:1200px;height:871px;overflow:hidden;background:#fff}
  body{position:relative;font-family:"Open Sans",Arial,sans-serif;color:var(--ink)}
  .leaflet{position:absolute;top:75px;width:510px;height:723px;background:linear-gradient(180deg,#fff 0%,var(--mist) 100%);overflow:hidden;box-shadow:0 2px 8px rgba(0,0,0,.25)}
  .leaflet--one{left:63px}
  .leaflet--two{left:628px}
  .shapes{position:absolute;inset:0;width:510px;height:723px}
  .abs{position:absolute}
  .photo{position:absolute;background:linear-gradient(160deg,var(--photo-b),var(--photo-a))}
  .photo--round{border-radius:50%;border:5px solid var(--purple)}
  .headline{font-family:"Oswald",sans-serif;font-weight:500;text-transform:uppercase}
  .headline span{display:block;line-height:1.02}
  .headline .b{color:var(--blue);font-size:20px}
  .headline .p{color:var(--pink);font-size:27px}
  .headline .s{color:var(--pink);font-size:17px}
  .brand{display:flex;align-items:center;gap:8px}
  .brand__dot{width:57px;height:57px;border-radius:50%;background:var(--pink);flex:none}
  .brand__name{font-family:"Oswald",sans-serif;font-weight:400;color:var(--blue);font-size:16px;line-height:1.05}
  .body-copy{font-size:7px;font-style:italic;line-height:1.4;text-align:justify;color:var(--muted)}
  .body-copy p{margin-bottom:9px}
  .callout{font-size:7.6px;color:var(--pink);text-transform:uppercase;line-height:1.4;font-style:normal;text-align:left}
  .criteria{text-align:right;font-size:7px;font-style:italic;line-height:1.35;color:var(--ink)}
  .criteria h2{font-family:"Oswald",sans-serif;font-weight:500;color:var(--pink);font-size:16px;line-height:1.05;font-style:normal;text-transform:uppercase;margin-bottom:9px}
  .criteria .lead{margin-bottom:9px}
  .criteria li{list-style:none;margin-bottom:7px;padding-right:12px;position:relative}
  .criteria li::after{content:"";position:absolute;right:0;top:3px;width:5px;height:5px;border-radius:50%;background:var(--pink)}
  .contact-line{font-size:7.4px;text-align:right;line-height:1.4;color:var(--ink)}
  .contact-line span{color:var(--blue)}
  .band{position:absolute;left:0;width:510px;height:8px;background:linear-gradient(90deg,var(--pink),var(--purple) 50%,var(--blue))}
  .pitch{font-size:8.6px;line-height:1.4}
  .pitch em{font-style:normal;color:var(--pink);font-size:9.6px}
  .footer-note{color:#fff;font-size:8.2px;font-weight:600;line-height:1.4}
  .big-title{font-family:"Oswald",sans-serif;font-weight:500;line-height:1}
  .big-title .p{color:var(--pink);font-size:33px;display:block}
  .big-title .b{color:var(--blue);font-size:21px;display:block;margin-top:3px}
  .copy{font-size:9.2px;line-height:1.3;color:var(--ink)}
  .copy p{margin-bottom:12px}
  .copy-zh{font-family:"Noto Sans TC",sans-serif;font-size:9.2px;line-height:1.35;color:var(--ink)}
  .copy-zh p{margin-bottom:11px}
  .pill{position:absolute;left:38px;top:495px;width:436px;height:32px;border-radius:16px;background:linear-gradient(90deg,var(--pink),var(--purple) 55%,var(--blue));color:#fff;font-family:"Noto Sans TC",sans-serif;font-size:7.6px;white-space:nowrap;display:flex;align-items:center;justify-content:center;padding:0 10px}
</style>
</head>
<body>

<section class="leaflet leaflet--one">
  <div class="photo" style="left:360px;top:0;width:150px;height:131px" role="img" aria-label="Photo of a smiling team of doctors in white coats"></div>

  <svg class="shapes" viewBox="0 0 510 723" aria-hidden="true">
    <defs>
      <linearGradient id="g1" x1="0" x2="1"><stop offset="0" stop-color="#e0479b"/><stop offset=".5" stop-color="#6b4b9e"/><stop offset="1" stop-color="#2f4b8f"/></linearGradient>
      <linearGradient id="g1v" x1="0" y1="1" x2="0" y2="0"><stop offset="0" stop-color="#e0479b"/><stop offset="1" stop-color="#6b4b9e"/></linearGradient>
    </defs>
    <path d="M0,104 C80,148 220,150 330,135" fill="none" stroke="url(#g1)" stroke-width="7"/>
    <path d="M276,0 C302,40 325,90 330,135" fill="none" stroke="#2f4b8f" stroke-width="10"/>
    <path d="M374,0 C348,40 333,90 330,135" fill="none" stroke="#2f4b8f" stroke-width="6"/>
    <path d="M330,135 C325,230 295,300 218,362" fill="none" stroke="url(#g1v)" stroke-width="5"/>
    <path d="M0,650 C140,600 300,660 510,585 L510,723 L0,723 Z" fill="url(#g1)"/>
    <path d="M0,628 C140,585 300,640 510,570" fill="none" stroke="#ffffff" stroke-width="6" opacity=".8"/>
  </svg>

  <h1 class="headline abs" style="left:31px;top:12px">
    <span class="b">Recruiting</span><span class="p">Healthy</span><span class="b">Volunteers</span><span class="s">And get paid</span>
  </h1>

  <div class="brand abs" style="left:140px;top:30px">
    <span class="brand__dot"></span>
    <span class="brand__name">Orient<br>Floracell<br>Reserve</span>
  </div>

  <div class="body-copy abs" style="left:24px;top:154px;width:292px">
    <p>The Orient Floracell Reserve is recruiting healthy individuals in Hong Kong to participate in a scientific research project to study bacteria in healthy guts. They will pay you $200 HKD per day to participate in the study. If you qualify, you can earn up to $4800 a month!</p>
    <p style="width:280px">Incidences of digestive and colon diseases are increasing rapidly in Hong Kong, and part of the key to solving this problem is understanding gut bacteria. There are up to 100 trillion bacteria and microbes in every human gut, including yours. Scientists have recently uncovered that these bacteria are key human digestion and immune systems. However, when your gut bacteria are imbalanced, it can cause all kinds of problems such as indigestion, IBS, ulcerative colitis, or clostridium difficile infection.</p>
    <p style="width:230px">Every year, more than 500,000 people are infected by a toxic bacteria called clostridium difficile, which causes severe stomach pain, and sometimes even death.</p>
    <p class="callout" style="width:190px">Your gut bacteria could be key to helping these sick patients.</p>
  </div>

  <div class="criteria abs" style="left:342px;top:143px;width:146px">
    <h2>Criteria for<br>participating</h2>
    <p class="lead">If you are a healthy adult between 18-50 years old:</p>
    <ul>
      <li>No digestive problems and no recent medications,</li>
      <li>Then the Orient VitaVault needs your participation!</li>
      <li>They will pay you $200 HKD per day to participate in the study.</li>
      <li>If you qualify, you can earn up to $4800 a month!</li>
    </ul>
  </div>

  <p class="contact-line abs" style="left:276px;top:322px;width:212px"><span>To learn more information, go to http://www.orientvitavault.example</span> or send a whatsapp to 7342 9086</p>

  <div class="band" style="top:362px"></div>

  <div class="photo photo--round" style="left:23px;top:397px;width:141px;height:141px" role="img" aria-label="Photo of a doctor consulting a patient"></div>
  <div class="photo photo--round" style="left:180px;top:388px;width:147px;height:147px" role="img" aria-label="Photo of a group of medical staff"></div>
  <div class="photo photo--round" style="left:345px;top:401px;width:139px;height:139px" role="img" aria-label="Photo of a doctor with a clipboard talking to a woman"></div>

  <p class="pitch abs" style="left:45px;top:566px;width:420px">Asia’s first commercial stool bank is recruiting donors. Get paid up to <em>$4,800 HKD</em> per month for your poop donations at our convenient Central Hong Kong lab.</p>

  <div class="photo" style="left:315px;top:594px;width:145px;height:107px;border-radius:4px" role="img" aria-label="Illustration of a laptop with a medical cross on screen"></div>

  <p class="footer-note abs" style="left:45px;top:667px;width:190px">Answer the questionnaire to see if you qualify at www.orientvitavault.example or call 7342 9086 for more information.</p>
</section>

<section class="leaflet leaflet--two">
  <div class="photo" style="left:195px;top:0;width:315px;height:221px" role="img" aria-label="Photo of three smiling doctors with stethoscopes"></div>

  <svg class="shapes" viewBox="0 0 510 723" aria-hidden="true">
    <defs>
      <linearGradient id="g2" x1="0" x2="1"><stop offset="0" stop-color="#e0479b"/><stop offset=".5" stop-color="#6b4b9e"/><stop offset="1" stop-color="#2f4b8f"/></linearGradient>
    </defs>
    <path d="M0,0 L232,0 C215,85 120,120 0,145 Z" fill="#ffffff"/>
    <path d="M232,0 C215,85 120,120 0,145" fill="none" stroke="#2f4b8f" stroke-width="8"/>
    <path d="M0,150 C60,200 150,232 260,226 C360,220 430,196 510,200 L510,240 L0,240 Z" fill="#ffffff"/>
    <path d="M0,150 C60,200 150,232 260,226 C360,220 430,196 510,200" fill="none" stroke="url(#g2)" stroke-width="9"/>
    <path d="M0,690 C150,660 320,705 510,672 L510,723 L0,723 Z" fill="url(#g2)"/>
  </svg>

  <h1 class="big-title abs" style="left:32px;top:27px">
    <span class="p">Get paid to</span><span class="b">give your poopoo!</span>
  </h1>

  <div class="brand abs" style="left:69px;top:140px">
    <span class="brand__dot"></span>
    <span class="brand__name">Orient<br>Floracell<br>Reserve</span>
  </div>

  <div class="copy abs" style="left:45px;top:250px;width:430px">
    <p>Literally.</p>
    <p>Asia’s first commercial stool bank is recruiting donors. Get paid up to $4,800 HKD per month for your poop donations at our convenient Central Hong Kong lab.</p>
    <p>Answer the questionnaire to see if you qualify at www.orientvitavault.example or call 7342 9086 for more information.</p>
  </div>

  <div class="band" style="top:364px"></div>

  <div class="copy-zh abs" style="left:45px;top:410px;width:430px" lang="zh-Hant">
    <p>你好屎!</p>
    <p>我地就係想要你D好屎。</p>
    <p>全亞洲第一間商業糞便銀行正招募捐贈者。請即前往我們位於中環的糞便銀行成為捐贈者，每月最多可賺取6,000港元的酬勞。</p>
  </div>

  <div class="pill" lang="zh-Hant">想知道自己是否適合捐贈?馬上點擊 www.orientvitavault.example/donate 回答問題或撥打0000-0000查詢詳情。</div>

  <div class="photo photo--round" style="left:39px;top:547px;width:154px;height:154px" role="img" aria-label="Photo of a smiling female patient with a doctor"></div>
  <div class="photo photo--round" style="left:220px;top:551px;width:141px;height:141px" role="img" aria-label="Photo of a smiling medical team"></div>
  <div class="photo" style="left:366px;top:538px;width:111px;height:185px;border-radius:50px 50px 0 0" role="img" aria-label="Photo of a standing female doctor in a white coat"></div>
</section>

</body>
</html>
```